SkyvornQ Business Cards and Stationary Design

Need a design for our business cards and stationary. I want to carry on the theme of the logo. I want the business cards to have a design on the back. I would like the business cards and the stationary to carry the same theme, design scheme, and branding

Target Market(s)

Airlines and Maintenance Facilities

Industry/Entity Type

Aviation

Contact Information for Business Card

Name
Position Title
Address: 4827 Trellis Hollow Road, Fort Pierce, Florida, 34951
Office Number
Mobile Number
Email
Website

Font styles to use
Serif
Sans Serif

Colors

Designer to choose colors to be used in the design.

```html
<!DOCTYPE html>
<html lang="en">
<head>
<meta charset="utf-8">
<title>SkyvornQ Business Card</title>
<link rel="stylesheet" href="https://fonts.googleapis.com/css2?family=Open+Sans:wght@400;600;700&display=swap">
<style>
  :root {
    --navy: #0c2a55;
    --navy-deep: #08203f;
    --blue: #1a7fd0;
    --sky: #1e9be0;
    --ink: #1d2b3a;
    --grey: #4a4f57;
    --paper: #ffffff;
    --backdrop: #eceef1;
  }
  * { margin: 0; padding: 0; box-sizing: border-box; }
  html, body {
    width: 1200px; height: 872px; overflow: hidden;
    background: var(--backdrop);
    font-family: "Open Sans", Arial, sans-serif;
  }
  .canvas { position: relative; width: 1200px; height: 872px; }

  .card {
    position: absolute; width: 560px; height: 320px;
    box-shadow: 0 10px 30px rgba(0,0,0,0.18);
    overflow: hidden;
  }

  /* Back side */
  .card-back {
    left: 60px; top: 80px;
    background: linear-gradient(135deg, var(--navy) 0%, var(--navy-deep) 100%);
    color: var(--paper);
  }
  .card-back .brand {
    position: absolute; left: 0; right: 0; top: 118px;
    display: flex; align-items: center; justify-content: center; gap: 16px;
  }
  .brand-dot {
    width: 44px; height: 44px; border-radius: 50%;
    border: 5px solid currentColor;
  }
  .card-back .brand-name {
    font-size: 40px; font-weight: 700; letter-spacing: 6px;
    text-transform: uppercase;
  }
  .card-back .web {
    position: absolute; left: 0; right: 0; top: 196px;
    text-align: center; font-size: 16px; letter-spacing: 3px;
  }

  /* Front side */
  .card-front {
    left: 600px; top: 470px;
    background: var(--paper);
    color: var(--ink);
  }
  .card-front .brand {
    position: absolute; left: 40px; top: 122px;
    display: flex; align-items: center; gap: 12px;
    color: var(--navy);
  }
  .card-front .brand-dot { width: 38px; height: 38px; border-width: 5px; border-color: var(--blue); }
  .card-front .brand-name {
    font-size: 30px; font-weight: 700; letter-spacing: 4px; text-transform: uppercase;
  }
  .person {
    position: absolute; right: 28px; top: 30px; text-align: right;
  }
  .person-name { font-size: 22px; font-weight: 700; color: var(--navy); letter-spacing: 0.3px; text-transform: uppercase; }
  .person-title { font-size: 18px; font-weight: 400; color: var(--grey); text-transform: uppercase; }

  .contacts {
    position: absolute; right: 28px; top: 118px;
    list-style: none; text-align: right;
  }
  .contacts li {
    display: flex; align-items: center; justify-content: flex-end; gap: 8px;
    font-size: 14px; color: var(--ink); line-height: 26px;
  }
  .contacts svg { width: 15px; height: 15px; flex: none; }

  .address-band {
    position: absolute; right: 0; bottom: 38px; width: 390px; height: 34px;
    background: linear-gradient(90deg, var(--sky) 0%, var(--navy) 100%);
    clip-path: polygon(22px 0, 100% 0, 100% 100%, 0 100%);
    display: flex; align-items: center; gap: 8px;
    padding-left: 30px; color: var(--paper); font-size: 12.5px;
    white-space: nowrap;
  }
  .address-band svg { width: 14px; height: 14px; flex: none; }
</style>
</head>
<body>
<main class="canvas">

  <section class="card card-back" aria-label="Card back">
    <div class="brand">
      <span class="brand-dot" aria-hidden="true"></span>
      <span class="brand-name">SkyvornQ</span>
    </div>
    <p class="web">www.skyvornq.com</p>
  </section>

  <section class="card card-front" aria-label="Card front">
    <div class="brand">
      <span class="brand-dot" aria-hidden="true"></span>
      <span class="brand-name">SkyvornQ</span>
    </div>

    <div class="person">
      <p class="person-name">Darren Kellaway</p>
      <p class="person-title">President</p>
    </div>

    <ul class="contacts">
      <li>772-418-3065
        <svg viewBox="0 0 16 16" aria-label="Office"><circle cx="8" cy="8" r="7" fill="none" stroke="#1a7fd0" stroke-width="1.4"/><path d="M5.5 4.5l1.5 1.5-.8 1a5 5 0 0 0 2.8 2.8l1-.8 1.5 1.5-1 1.2c-2.6-.3-5-2.7-5.3-5.3z" fill="#1a7fd0"/></svg>
      </li>
      <li>772-904-2617
        <svg viewBox="0 0 16 16" aria-label="Mobile"><circle cx="8" cy="8" r="7" fill="none" stroke="#1a7fd0" stroke-width="1.4"/><rect x="5.6" y="4" width="4.8" height="8" rx="1" fill="none" stroke="#1a7fd0" stroke-width="1.3"/></svg>
      </li>
      <li>info@skyvornq.com
        <svg viewBox="0 0 16 16" aria-label="Email"><circle cx="8" cy="8" r="7" fill="none" stroke="#1a7fd0" stroke-width="1.4"/><rect x="4.3" y="5.3" width="7.4" height="5.4" fill="none" stroke="#1a7fd0" stroke-width="1.2"/><path d="M4.3 5.3L8 8.3l3.7-3" fill="none" stroke="#1a7fd0" stroke-width="1.2"/></svg>
      </li>
      <li>www.skyvornq.com
        <svg viewBox="0 0 16 16" aria-label="Website"><circle cx="8" cy="8" r="7" fill="none" stroke="#1a7fd0" stroke-width="1.4"/><ellipse cx="8" cy="8" rx="2.6" ry="7" fill="none" stroke="#1a7fd0" stroke-width="1.1"/><path d="M1 8h14" stroke="#1a7fd0" stroke-width="1.1"/></svg>
      </li>
    </ul>

    <div class="address-band">
      <svg viewBox="0 0 16 16" aria-label="Address"><circle cx="8" cy="8" r="7" fill="none" stroke="#fff" stroke-width="1.3"/><path d="M8 3.8a2.7 2.7 0 0 0-2.7 2.7C5.3 8.6 8 12 8 12s2.7-3.4 2.7-5.5A2.7 2.7 0 0 0 8 3.8z" fill="#fff"/><circle cx="8" cy="6.5" r="1" fill="#1e9be0"/></svg>
      <span>4827 Trellis Hollow Road, Fort Pierce, Florida, 34951</span>
    </div>
  </section>

</main>
</body>
</html>
```